Logo, Web and Mobile Designs for enterprise social media platform

All the details are in the attached document, please start reading the scope document first which explains what is this project about and the details about the needed deliverables, after that please read the UI_Requirements document which will detail what is expected regarding the coded web version since this is a coded contest, it is very important that you meet the UI requirements or suggest something else but we will need to agree first before working on the coded version

Good Luck

Target Market(s)

Enterprise Social Media

Industry/Entity Type

Media

Coding

Coded - Design and coding required

Number of Pages Required

5+ page

Font styles to use
Sans Serif

Requirements
Must have
• All the must haves are listed in the scope document so please check before you start

```html
<!DOCTYPE html>
<html lang="en">
<head>
<meta charset="utf-8">
<title>Teamora — Social Media Platform</title>
<link rel="stylesheet" href="https://fonts.googleapis.com/css2?family=Ubuntu:wght@300;400;500;700&family=Open+Sans:ital,wght@0,400;0,600;0,700;1,400&family=Playfair+Display:wght@700&display=swap">
<style>
:root{
  --accent:#d3214f;
  --dark:#3d3d3d;
  --topbar:#333333;
  --footer:#232323;
  --bottom:#151515;
  --text:#333333;
  --muted:#8a8a8a;
  --line:#e2e2e2;
  --panel:#f1f1f1;
  --link:#2f7fc9;
  --online:#3bb44a;
  --orange:#f0922b;
}
*{box-sizing:border-box;margin:0;padding:0}
html,body{width:1200px;height:2744px;overflow:hidden}
body{position:relative;background:#fff;font-family:"Open Sans",Arial,sans-serif;color:var(--text);font-size:13px}
.abs{position:absolute}
ul{list-style:none}

/* top bar */
.topbar{top:0;left:0;width:1200px;height:46px;background:var(--topbar);color:#fff;font-size:13px}
.topbar .item{position:absolute;top:0;height:46px;display:flex;align-items:center;gap:9px}
.badge{position:absolute;top:6px;right:-8px;width:17px;height:17px;border-radius:50%;background:var(--accent);font-size:10px;display:flex;align-items:center;justify-content:center;border:1px solid #fff}

/* nav */
.nav{top:46px;left:0;width:1200px;height:82px;background:#fff}
.brand{position:absolute;left:86px;top:17px;display:flex;align-items:center;gap:12px;font-family:"Ubuntu",sans-serif;font-weight:500;font-size:25px;color:#333}
.brand .dot{width:48px;height:48px;border-radius:50%;background:var(--accent)}
.menu{position:absolute;right:86px;top:27px;display:flex;gap:14px;font-size:13px;text-transform:uppercase}
.menu li{padding:8px 13px;border-radius:4px}
.menu li.active{background:var(--accent);color:#fff}

/* hero */
.hero{top:128px;left:0;width:1200px;height:545px;background:linear-gradient(180deg,#5a4f86 0%,#6b5b8e 35%,#8b6f8c 55%,#2b2d4a 75%,#1a1c30 100%)}
.hero-mark{position:absolute;left:572px;top:56px;width:56px;height:56px;border-radius:50%;background:rgba(255,255,255,.35)}
.tagline{position:absolute;top:157px;left:0;width:1200px;text-align:center;font-family:"Playfair Display",serif;font-weight:700;font-size:31px;color:#fff;letter-spacing:1px}
.tagline-rule{position:absolute;top:174px;width:170px;height:5px;border-top:1px solid rgba(255,255,255,.7);border-bottom:1px solid rgba(255,255,255,.7)}
.hero-title{position:absolute;top:218px;left:0;width:1200px;text-align:center;font-family:"Ubuntu",sans-serif;font-weight:700;font-size:46px;color:#fff}
.btn{position:absolute;top:302px;height:51px;display:flex;align-items:center;justify-content:center;gap:12px;font-size:20px;color:#fff;text-transform:uppercase;font-family:"Open Sans",sans-serif}
.btn-primary{left:404px;width:174px;background:var(--accent);border-radius:3px}
.btn-outline{left:609px;width:174px;border:1px solid #fff;border-radius:2px}
.dots{position:absolute;top:510px;left:0;width:1200px;display:flex;justify-content:center;gap:24px}
.dots span{width:12px;height:12px;border-radius:50%;background:#fff}
.dots span.off{background:transparent;border:2px solid #fff}

/* section heading */
.sec-head{display:flex;align-items:center;gap:14px;font-family:"Ubuntu",sans-serif;font-size:23px;color:#222}
.sec-head b{font-weight:700;text-transform:uppercase}
.sec-head .sub{font-weight:300}
.sec-icon{width:34px;height:34px;border-radius:50%;background:var(--accent);display:flex;align-items:center;justify-content:center}

.about-text{top:775px;left:86px;width:669px;font-size:12.5px;line-height:23.5px;color:#444}
.read-more{top:913px;left:86px;width:146px;height:41px;background:var(--accent);border-radius:3px;color:#fff;font-size:16px;display:flex;align-items:center;justify-content:center;gap:10px}

/* tabs */
.tabs-box{top:991px;left:86px;width:669px;height:400px;border:1px solid var(--line);border-radius:4px}
.tab{position:absolute;top:14px;height:36px;border-radius:18px;border:1px solid #777;font-size:15px;display:flex;align-items:center;justify-content:center;color:#333}
.tab.active{background:var(--accent);border-color:var(--accent);color:#fff}
.feature-photo{position:absolute;left:16px;top:69px;width:306px;height:309px;background:linear-gradient(160deg,#d9b78a 0%,#c79560 40%,#7e8c9e 100%)}
.story{position:absolute;left:346px;display:flex;gap:14px}
.story .thumb{width:86px;height:86px}
.story h4{font-size:15px;font-weight:600;line-height:22px;color:#222;width:210px;margin-top:6px}
.story time{display:block;font-size:11px;color:var(--muted);margin-top:10px}

/* posts */
.posts{top:1429px;left:86px;width:669px;height:680px;background:var(--panel);border-radius:16px;border-bottom:6px solid var(--dark);overflow:hidden}
.posts-head{height:57px;background:var(--dark);color:#fff;font-size:16px;display:flex;align-items:center;padding:0 52px 0 42px;gap:20px}
.posts-head .tabi{display:flex;align-items:center;gap:10px;white-space:nowrap}
.posts-head .rule{flex:1;height:1px;background:#888}
.ico-w{width:18px;height:18px;border-radius:50%;background:#fff;display:flex;align-items:center;justify-content:center}
.avatar-lg{position:absolute;left:27px;width:96px;height:96px;border-radius:50%;border:5px solid #c9c9c9;background:linear-gradient(180deg,#e4d7cc,#b8a899)}
.post-card{position:absolute;left:152px;width:490px;height:176px;background:#fff;border:1px solid #dadada;border-radius:6px;padding:16px 20px}
.post-card h3{font-size:16px;font-weight:700;color:var(--accent);padding-bottom:10px;border-bottom:1px solid var(--line)}
.post-card p{font-size:12.5px;line-height:18px;color:#666;margin-top:12px}
.share{position:absolute;right:8px;top:10px;width:24px;height:24px;border-radius:50%;border:2px solid var(--accent)}
.meta{position:absolute;left:20px;bottom:14px;font-size:10px;color:var(--muted);font-style:italic;display:flex;gap:14px}
.soc{position:absolute;right:12px;bottom:10px;display:flex;gap:6px}
.soc span{width:24px;height:24px;border-radius:50%;background:#6c6c6c}
.soc span:nth-child(2){background:#8f8f8f}
.soc span:nth-child(3){background:var(--accent)}
.soc span:nth-child(4){background:#a41c40}

/* sidebar */
.widget{left:807px;width:307px;border:1px solid var(--line);background:#fff}
.widget-head{height:38px;background:var(--dark);color:#fff;font-family:"Ubuntu",sans-serif;font-weight:500;font-size:16px;display:flex;align-items:center;padding-left:12px;text-transform:uppercase}
.search{position:absolute;left:25px;top:53px;width:256px;height:29px;border:1px solid #dcdcdc;border-radius:3px;font-size:10px;color:#aaa;padding:7px 10px}
.chat{position:absolute;left:25px;width:256px;display:flex;align-items:center;gap:11px}
.chat .av{position:relative;width:36px;height:36px;border-radius:50%;background:#9a8e84}
.chat .av i{position:absolute;right:-1px;bottom:-1px;width:11px;height:11px;border-radius:50%;background:var(--online);border:2px solid #fff}
.chat b{display:block;font-weight:400;font-size:14px;color:#333}
.chat small{font-size:11px;color:#aaa}
.chat .act{margin-left:auto;width:25px;height:25px;border-radius:50%;border:1.5px solid #bbb;display:flex;align-items:center;justify-content:center}
.profile{position:absolute;left:16px;display:flex;gap:15px}
.profile .pic{width:80px;height:80px}
.profile h4{font-size:13.5px;font-weight:600;line-height:19px;color:#222;width:190px;margin-top:6px}
.profile time{display:block;font-size:11px;color:var(--muted);margin-top:6px}
.tweet{position:absolute;left:16px;width:276px;display:flex;gap:10px;font-size:12.5px;line-height:18px;color:#333}
.tweet .bd{width:9px;height:9px;border-radius:50%;background:var(--link);margin-top:5px;flex:none}
.tweet a{color:var(--link);text-decoration:none}
.tweet time{display:block;text-align:right;font-size:11px;color:var(--muted);margin-top:4px}
.social-row{position:absolute;top:70px;left:18px;display:flex;gap:24px}
.social-row span{width:37px;height:37px;border-radius:50%;background:#555}

/* sponsors */
.arrow-btn{top:2186px;width:27px;height:27px;border:1px solid #999;border-radius:3px;display:flex;align-items:center;justify-content:center}
.sponsor{top:2243px;width:220px;height:103px;border:1px solid var(--line);display:flex;align-items:center;justify-content:center;font-size:18px;font-weight:600;color:#555}

/* footer */
.footer{top:2384px;left:0;width:1200px;height:302px;background:var(--footer);color:#ccc}
.f-head{position:absolute;top:56px;font-family:"Ubuntu",sans-serif;font-weight:500;font-size:17px;color:#fff;text-transform:uppercase;width:148px;padding-bottom:8px;border-bottom:1px solid #666}
.f-head::after{content:"";position:absolute;left:0;bottom:-1px;width:70px;height:2px;background:var(--accent)}
.f-line{position:absolute;left:86px;font-size:12px;display:flex;gap:12px;line-height:22px}
.news{position:absolute;left:342px;display:flex;gap:20px;font-size:12px;line-height:20px}
.date{width:51px;text-align:center;font-size:11px;color:#fff}
.date b{display:block;background:var(--accent);font-weight:600;height:20px;line-height:20px;border-radius:3px 3px 0 0}
.date span{display:block;background:#555;font-size:16px;height:32px;line-height:32px}
.qlinks{position:absolute;left:618px;top:110px;font-size:13px;color:#fff}
.qlinks li{height:28.7px;display:flex;align-items:center;gap:14px}
.qlinks li::before{content:"";width:5px;height:5px;border-radius:50%;background:#fff}
.map{position:absolute;left:814px;top:53px;width:300px;height:191px;background:linear-gradient(135deg,#e6e3da 0%,#dcd8cf 55%,#b8cde0 100%)}
.bottom{top:2686px;left:0;width:1200px;height:58px;background:var(--bottom);color:#ccc;font-size:12px;display:flex;align-items:center;justify-content:center}
</style>
</head>
<body>

<header class="abs topbar">
  <div class="item" style="left:86px">
    <svg width="14" height="11" viewBox="0 0 14 11"><rect x="0.5" y="0.5" width="13" height="10" fill="#fff"/><path d="M1 1l6 5 6-5" stroke="#333" fill="none"/></svg>info@teamora.com
  </div>
  <div class="item" style="left:256px">
    <svg width="13" height="13" viewBox="0 0 13 13"><rect width="13" height="13" rx="2" fill="#fff"/><path d="M4 3l2 2-1 1c1 1 1 1 2 2l1-1 2 2-1 1C6 10 3 7 3 4z" fill="#333"/></svg>+6231 402 555 010
  </div>
  <div class="item" style="left:855px">Message
    <span style="position:relative;display:inline-block;width:20px;height:18px">
      <svg width="20" height="18" viewBox="0 0 20 18"><path d="M10 2C5 2 2 5 2 8c0 2 1 3 2 4l-1 4 4-2c1 0 2 1 3 1 5 0 8-3 8-7s-3-6-8-6z" fill="none" stroke="#fff" stroke-width="1.5"/></svg>
      <span class="badge">5</span>
    </span>
  </div>
  <div class="item" style="left:1004px">My Account
    <svg width="12" height="13" viewBox="0 0 12 13"><circle cx="6" cy="3.5" r="3" fill="#fff"/><path d="M0 13c0-4 2.5-6 6-6s6 2 6 6z" fill="#fff"/></svg>
  </div>
</header>

<nav class="abs nav">
  <div class="brand"><span class="dot"></span>Teamora</div>
  <ul class="menu">
    <li class="active">Home</li><li>About</li><li>Events</li><li>Media</li><li>Price</li><li>Blog</li><li>Contact</li>
  </ul>
</nav>

<section class="abs hero" role="img" aria-label="Night city skyline photograph under a purple dusk sky">
  <div class="hero-mark"></div>
  <div class="tagline-rule" style="left:213px"></div>
  <div class="tagline">GET CONNECTED WITH US</div>
  <div class="tagline-rule" style="left:817px"></div>
  <h1 class="hero-title">SOCIAL MEDIA PLATFORM</h1>
  <div class="btn btn-primary">Register
    <svg width="20" height="20" viewBox="0 0 20 20"><circle cx="10" cy="10" r="9" fill="#fff"/><path d="M7 10h6M10 7l3 3-3 3" stroke="#d3214f" stroke-width="2" fill="none"/></svg>
  </div>
  <div class="btn btn-outline">Watch Video</div>
  <div class="dots"><span></span><span class="off"></span><span></span></div>
</section>

<div class="abs sec-head" style="top:716px;left:86px">
  <span class="sec-icon"><svg width="16" height="16" viewBox="0 0 16 16"><path d="M8 1l2 5h5l-4 3 2 6-5-4-5 4 2-6-4-3h5z" fill="#fff"/></svg></span>
  <span><b>What's About Event</b> <span class="sub">/ Join With Us</span></span>
</div>
<p class="abs about-text">Praesent ac sem in neque venenatis tristique. Morbi et ligula velit. Nullam a augue vel mi porta vestibulum non ac elit. Vivamus convallis tortor et fermentum semper. In hac habitasse platea dictumst. Curabitur eget dui id metus pulvinar suscipit. Quisque vitae ligula laoreet, scelerisque leo quis, facilisis metus. Sed pellentesque, urna sed varius consectetur, eros augue fringilla magna, id sem magna vel diam. Nulla sed hendrerit nunc.</p>
<div class="abs read-more">Read More
  <svg width="18" height="18" viewBox="0 0 20 20"><circle cx="10" cy="10" r="9" fill="#fff"/><path d="M7 10h6M10 7l3 3-3 3" stroke="#d3214f" stroke-width="2" fill="none"/></svg>
</div>

<section class="abs tabs-box">
  <div class="tab active" style="left:16px;width:136px">Most Recent</div>
  <div class="tab" style="left:172px;width:132px">Top Events</div>
  <div class="tab" style="left:326px;width:133px">Top Events</div>
  <div class="feature-photo" role="img" aria-label="Photo of smiling students holding books"></div>
  <div class="story" style="top:69px"><div class="thumb" role="img" aria-label="Photo of people at a meeting" style="background:linear-gradient(135deg,#8fb7c4,#c9a07e)"></div><div><h4>Excepteur sint occaecat cupidatat proident</h4><time>November 03, 2015</time></div></div>
  <div class="story" style="top:183px"><div class="thumb" role="img" aria-label="Photo of a lecture" style="background:linear-gradient(135deg,#c8bfb3,#7f6b5c)"></div><div><h4>Excepteur sint occaecat cupidatat proident</h4><time>November 03, 2015</time></div></div>
  <div class="story" style="top:296px"><div class="thumb" role="img" aria-label="Photo of a classroom board" style="background:linear-gradient(135deg,#4f8a6a,#2e5c47)"></div><div><h4>Excepteur sint occaecat cupidatat proident</h4><time>November 03, 2015</time></div></div>
</section>

<section class="abs posts">
  <div class="posts-head">
    <span class="tabi"><span class="ico-w"><svg width="10" height="10" viewBox="0 0 10 10"><path d="M2 8l1-3 4-4 2 2-4 4z" fill="#3d3d3d"/></svg></span>Post Events</span>
    <span class="rule"></span>
    <span class="tabi"><span class="ico-w"></span>Post Comments</span>
    <span class="rule"></span>
    <span class="tabi"><span class="ico-w"></span>Chats</span>
  </div>

  <div class="avatar-lg" role="img" aria-label="Member portrait" style="top:82px"></div>
  <article class="post-card" style="top:82px">
    <span class="share"></span>
    <h3>Perspiciatis Unde Omnis Istenatus</h3>
    <p>Lorem ipsum dolor sit amet, consectetur adipiscing elit. Sed vitae diam metus. Donec cursus magna eget sem convallis facilisis. Vestibulum dictum nibh at ullamcorper tincidunt.</p>
    <div class="meta"><span>Samir Halden</span><span>8</span><span>2K</span></div>
    <div class="soc"><span></span><span></span><span></span><span></span></div>
  </article>

  <div class="avatar-lg" role="img" aria-label="Member portrait" style="top:280px"></div>
  <article class="post-card" style="top:280px">
    <span class="share"></span>
    <h3>Perspiciatis Unde Omnis Istenatus</h3>
    <p>Lorem ipsum dolor sit amet, consectetur adipiscing elit. Sed vitae diam metus. Donec cursus magna eget sem convallis facilisis. Vestibulum dictum nibh at ullamcorper tincidunt.</p>
    <div class="meta"><span>Samir Halden</span><span>8</span><span>2K</span></div>
    <div class="soc"><span></span><span></span><span></span><span></span></div>
  </article>

  <div class="avatar-lg" role="img" aria-label="Member portrait" style="top:477px"></div>
  <article class="post-card" style="top:477px">
    <span class="share"></span>
    <h3>Perspiciatis Unde Omnis Istenatus</h3>
    <p>Lorem ipsum dolor sit amet, consectetur adipiscing elit. Sed vitae diam metus. Donec cursus magna eget sem convallis facilisis. Vestibulum dictum nibh at ullamcorper tincidunt.</p>
    <div class="meta"><span>Samir Halden</span><span>8</span><span>2K</span></div>
    <div class="soc"><span></span><span></span><span></span><span></span></div>
  </article>
</section>

<aside class="abs widget" style="top:715px;height:390px">
  <div class="widget-head">People in Chat</div>
  <div class="search">Search</div>
  <div class="chat" style="top:112px"><span class="av" role="img" aria-label="Avatar"><i></i></span><span><b>Owen Castell</b><small>1 hour ago</small></span><span class="act"><svg width="11" height="11"><path d="M5.5 1v9M1 5.5h9" stroke="#bbb" stroke-width="1.4"/></svg></span></div>
  <div class="chat" style="top:180px"><span class="av" role="img" aria-label="Avatar"></span><span><b>Ravi Dalmet</b><small>5 min ago</small></span><span class="act"><svg width="11" height="11"><path d="M5.5 1v9M1 5.5h9" stroke="#bbb" stroke-width="1.4"/></svg></span></div>
  <div class="chat" style="top:249px"><span class="av" role="img" aria-label="Avatar"></span><span><b>Glen Varrow</b><small>12 min ago</small></span><span class="act" style="border-color:var(--orange)"><svg width="12" height="10"><path d="M1 5l3.5 3.5L11 1" stroke="#f0922b" stroke-width="1.6" fill="none"/></svg></span></div>
  <div class="chat" style="top:317px"><span class="av" role="img" aria-label="Avatar"><i></i></span><span><b>Marco Vellini</b><small>1 hour ago</small></span><span class="act"><svg width="11" height="11"><path d="M5.5 1v9M1 5.5h9" stroke="#bbb" stroke-width="1.4"/></svg></span></div>
</aside>

<aside class="abs widget" style="top:1136px;height:339px">
  <div class="widget-head">Top User Profiles</div>
  <div class="profile" style="top:56px"><div class="pic" role="img" aria-label="Member photo" style="background:linear-gradient(135deg,#d8c0ac,#8c6a55)"></div><div><h4>Nemo enim ipsam volptatem quia voluptas</h4><time>November 03, 2015</time></div></div>
  <div class="profile" style="top:151px"><div class="pic" role="img" aria-label="Member photo" style="background:linear-gradient(135deg,#d9c45c,#a8864c)"></div><div><h4>Nemo enim ipsam volptatem quia voluptas</h4><time>November 03, 2015</time></div></div>
  <div class="profile" style="top:246px"><div class="pic" role="img" aria-label="Member photo" style="background:linear-gradient(135deg,#a86e5c,#5e3a30)"></div><div><h4>Nemo enim ipsam volptatem quia voluptas</h4><time>November 03, 2015</time></div></div>
</aside>

<aside class="abs widget" style="top:1506px;height:440px">
  <div class="widget-head">Live Feed</div>
  <div class="tweet" style="top:53px"><span class="bd"></span><div><a>@smallberry</a> Hey. Our VPS down for more than 3 Hours and your live support is putting us in queue where it ends on connection error.<time>15 days ago</time></div></div>
  <div class="tweet" style="top:148px"><span class="bd"></span><div><a>@smallberry</a> Hey. Our VPS down for more than 3 Hours and your live support is putting us in queue where it ends on connection error.<time>15 days ago</time></div></div>
  <div class="tweet" style="top:243px"><span class="bd"></span><div><a>@smallberry</a> Hey. Our VPS down for more than 3 Hours and your live support is putting us in queue where it ends on connection error.<time>15 days ago</time></div></div>
  <div class="tweet" style="top:338px"><span class="bd"></span><div><a>@smallberry</a> Hey. Our VPS down for more than 3 Hours and your live support is putting us in queue where it ends on connection error.<time>15 days ago</time></div></div>
</aside>

<aside class="abs widget" style="top:1976px;height:137px">
  <div class="widget-head">Stay Connected</div>
  <div class="social-row"><span></span><span style="background:#777"></span><span style="background:var(--accent)"></span><span style="background:#999"></span><span style="background:var(--orange)"></span></div>
</aside>

<div class="abs sec-head" style="top:2164px;left:86px">
  <span class="sec-icon"><svg width="16" height="16" viewBox="0 0 16 16"><path d="M8 1l2 5h5l-4 3 2 6-5-4-5 4 2-6-4-3h5z" fill="#fff"/></svg></span>
  <span><b>Event Sponsors</b> <span class="sub">/ dont forget it</span></span>
</div>
<div class="abs arrow-btn" style="left:1042px"><svg width="8" height="10"><path d="M7 0v10L0 5z" fill="#333"/></svg></div>
<div class="abs arrow-btn" style="left:1087px"><svg width="8" height="10"><path d="M1 0v10l7-5z" fill="#333"/></svg></div>
<div class="abs sponsor" style="left:86px">Crestline Supply</div>
<div class="abs sponsor" style="left:357px">Harbor Vale Limited</div>
<div class="abs sponsor" style="left:626px">Ashgrove Partners</div>
<div class="abs sponsor" style="left:894px">K.L. Bramwell</div>

<footer class="abs footer">
  <h5 class="f-head" style="left:86px">Contact Us</h5>
  <div class="f-line" style="top:108px"><svg width="9" height="12" style="margin-top:5px"><path d="M4.5 0C2 0 0 2 0 4.5 0 8 4.5 12 4.5 12S9 8 9 4.5C9 2 7 0 4.5 0z" fill="#ccc"/></svg><span>Address: 14 Linden Row,<br>Marlow Heights, Aveland</span></div>
  <div class="f-line" style="top:169px"><svg width="10" height="12" style="margin-top:5px"><rect width="10" height="12" rx="2" fill="#ccc"/></svg><span>Phone: +0401 555 270</span></div>
  <div class="f-line" style="top:203px"><svg width="12" height="9" style="margin-top:7px"><rect x=".5" y=".5" width="11" height="8" fill="none" stroke="#ccc"/><path d="M1 1l5 4 5-4" stroke="#ccc" fill="none"/></svg><span>Email: info@teamora.in</span></div>

  <h5 class="f-head" style="left:342px">Recent News</h5>
  <div class="news" style="top:110px"><div class="date"><b>OCT</b><span>25</span></div><p>Pellentesque om are sem<br>quam venenatis</p></div>
  <div class="news" style="top:187px"><div class="date"><b>OCT</b><span>28</span></div><p>Pellentesque om are sem<br>quam venenatis</p></div>

  <h5 class="f-head" style="left:618px">Quick Links</h5>
  <ul class="qlinks"><li>HOME</li><li>EVENTS</li><li>MEDIA</li><li>PRICE</li><li>BLOG</li></ul>

  <div class="map" role="img" aria-label="Street map showing the office location"></div>
</footer>
<div class="abs bottom">© 2015 All rights reserved. TEAMORA</div>

</body>
</html>
```